Dwelvano - "Where Pest Control is Free for Life..." Please see pitch deck...

Project goal, that this is a reusable template, not a one-off card
Brand and design direction, follow the logo, use the brand palette (with a color swatch table), typography and layout guidance
The John Doe placeholder content as a clean field-by-field table (name, title, company, address, office, cell, fax, email, dwelvano.com)
Print specs, 3.5 × 2 in trim, 0.125 in bleed, 300 DPI, CMYK, crop marks
Deliverables, layered editable PSD (your primary ask) plus vector .AI/.EPS and a press-ready PDF/X-1a, with fonts packaged
What you'll provide (logo, colors, fonts)
Process and sign-off, concept first, then full file package on approval.
Populate every field with this John Doe placeholder data so we can see the layout fully built out. We will replace it per person.
Name John Doe
Title Title / Position
Company Dwelvano
Address 48 Harbor Lane, Suite 210, Gainesville, FL 32601
Office (904) 555-0142
Cell (904) 555-0187
Fax (904) 555-0163
Email johndoe@dwelvano.com
Website dwelvano.com

We need the working, editable source files so we can update them ourselves, plus a ready-to-print export:
1. Photoshop (.PSD) — fully layered and editable, with each contact field on its own labeled text layer. This is the primary requested format.
2. Vector source — the press-standard editable format, Adobe Illustrator (.AI) and/or .EPS, since vector is preferred for crisp text and logos at print.
3. Print-ready PDF — press-quality (PDF/X-1a), CMYK, with bleed and crop marks, both sides.
4. Packaged fonts and links — include or list all fonts used, and package any linked assets so the files open correctly on our end.

Why both PSD and vector
The PSD covers our request directly and is easy for us to edit. Vector (.AI/.EPS) is what most commercial printers actually prefer for type and logos because it stays razor-sharp at any size. Providing both keeps us flexible no matter which printer we use. Have fun and keep it modern and cool the designer of the logo did a great job, see what you can do.

```html
<!DOCTYPE html>
<html lang="en">
<head>
<meta charset="utf-8">
<title>Dwelvano — Business Card, Front and Back</title>
<link rel="stylesheet" href="https://fonts.googleapis.com/css2?family=Poppins:ital,wght@0,400;0,500;0,600;0,700;1,400&display=swap">
<style>
  :root {
    --page-bg: #f1f1f1;
    --card-navy: #0a1326;
    --brand-teal: #04b3c6;
    --text-white: #ffffff;
    --card-w: 712px;
    --card-h: 407px;
    --card-radius: 46px;
  }
  * { margin: 0; padding: 0; box-sizing: border-box; }
  html, body {
    width: 1200px; height: 990px; overflow: hidden;
    background: var(--page-bg);
    font-family: "Poppins", sans-serif;
  }
  .card {
    position: absolute; left: 244px;
    width: var(--card-w); height: var(--card-h);
    background: var(--card-navy);
    border-radius: var(--card-radius);
    overflow: hidden;
  }
  .card--front { top: 68px; }
  .card--back { top: 516px; }

  .edge-bar {
    position: absolute; top: 102px;
    width: 16px; height: 203px;
    background: var(--brand-teal);
  }
  .edge-bar--left { left: 0; }
  .edge-bar--right { right: 0; }

  .wordmark {
    position: absolute;
    font-weight: 700;
    letter-spacing: -0.02em;
    line-height: 1;
    white-space: nowrap;
  }
  .card--front .wordmark {
    left: 0; right: 0; top: 176px;
    text-align: center;
    font-size: 64px;
    color: var(--brand-teal);
  }
  .card--back .wordmark {
    left: 37px; top: 172px;
    font-size: 54px;
    color: var(--text-white);
  }

  .tagline {
    position: absolute; left: 38px; top: 220px;
    font-size: 12.5px; font-weight: 700; line-height: 18px;
    letter-spacing: 0.08em;
    color: var(--text-white);
  }
  .subline {
    position: absolute; left: 88px; top: 234px;
    font-size: 10.5px; font-style: italic; line-height: 14px;
    color: var(--brand-teal);
    letter-spacing: 0.02em;
  }

  .divider {
    position: absolute; left: 356px; top: 80px;
    width: 1px; height: 246px;
    background: var(--brand-teal);
    opacity: 0.8;
  }

  .person { position: absolute; left: 407px; top: 99px; }
  .person__name {
    font-size: 37px; line-height: 1; color: var(--text-white);
    font-weight: 400; letter-spacing: 0.01em;
  }
  .person__first { color: var(--brand-teal); font-weight: 600; }
  .person__title {
    margin-top: 2px;
    font-size: 18px; font-weight: 500; color: var(--text-white);
  }

  .contact-list {
    position: absolute; left: 405px; top: 174px;
    list-style: none;
  }
  .contact-list li {
    display: flex; align-items: center;
    height: 24px;
    font-size: 18.5px; color: var(--text-white);
    letter-spacing: 0.02em;
  }
  .contact-list svg {
    width: 17px; height: 17px; margin-right: 10px; flex: none;
    fill: none; stroke: var(--brand-teal); stroke-width: 1.8;
  }

  .address {
    position: absolute; left: 0; right: 0; top: 351px;
    text-align: center;
    font-size: 18px; color: var(--brand-teal);
    letter-spacing: 0.02em;
  }
</style>
</head>
<body>

<section class="card card--front" aria-label="Card front">
  <span class="edge-bar edge-bar--left"></span>
  <span class="edge-bar edge-bar--right"></span>
  <h1 class="wordmark">Dwelvano.com</h1>
</section>

<section class="card card--back" aria-label="Card back">
  <span class="edge-bar edge-bar--left"></span>
  <span class="edge-bar edge-bar--right"></span>

  <div class="wordmark">Dwelvano</div>
  <p class="tagline">PEST CONTROL FREE FOR LIFE</p>
  <p class="subline">Protecting every household</p>

  <span class="divider"></span>

  <div class="person">
    <p class="person__name"><span class="person__first">John</span> Doe</p>
    <p class="person__title">Title / Position</p>
  </div>

  <ul class="contact-list">
    <li>
      <svg viewBox="0 0 24 24" aria-hidden="true"><path d="M5 3h4l2 5-2.5 1.5a11 11 0 0 0 6 6L16 13l5 2v4a2 2 0 0 1-2 2A16 16 0 0 1 3 5a2 2 0 0 1 2-2z"/></svg>
      (904) 555-0142
    </li>
    <li>
      <svg viewBox="0 0 24 24" aria-hidden="true"><rect x="7" y="2" width="10" height="20" rx="2"/><path d="M11 18h2"/></svg>
      (904) 555-0187
    </li>
    <li>
      <svg viewBox="0 0 24 24" aria-hidden="true"><rect x="3" y="9" width="18" height="12" rx="1"/><path d="M7 9V3h8l2 2v4M7 13h2M11 13h2M15 13h2M7 17h2M11 17h2M15 17h2"/></svg>
      (904) 555-0163
    </li>
    <li>
      <svg viewBox="0 0 24 24" aria-hidden="true"><circle cx="12" cy="12" r="9"/><path d="M3 12h18M12 3c3 3 3 15 0 18M12 3c-3 3-3 15 0 18"/></svg>
      www.dwelvano.com
    </li>
    <li>
      <svg viewBox="0 0 24 24" aria-hidden="true"><path d="M3 10l9-6 9 6v10H3z"/><path d="M3 10l9 6 9-6"/></svg>
      johndoe@dwelvano.com
    </li>
  </ul>

  <p class="address">48 Harbor Lane, Suite 210, Gainesville, FL 32601</p>
</section>

</body>
</html>
```